Super elegant, crisp & clean Business card design required

We recently upgraded our branding - which is on our website - talvendoraphoto.com

I would like a simple, yet elegant, clean business card design please.

The font of my logo is Cinzel - and because of the natural colour - it's best to have this on a black background.

I would like to have the back of the business card - with simply my logo.

PLEASE DO NOT SUBMIT A COMPLICATED / UNCLEAN DESIGN

Industry/Entity Type

Business

Contact Information for Business Card

Talven Doroshko Photography

Font styles to use
Other font styles liked:
• Cinzel

Requirements
Must have
• A backpage with nothing but my logo
• Simple design - stands out
Should not have
• Colour that dont align with my logo
• Over complicated '/ non symmetrical design

```html
<!DOCTYPE html>
<html lang="en">
<head>
<meta charset="utf-8">
<title>Talven Doroshko Photography – Business Card</title>
<link href="https://fonts.googleapis.com/css2?family=Cinzel:wght@400&family=Questrial&display=swap" rel="stylesheet">
<style>
  :root {
    --page-bg: #e8e5e1;
    --card-black: #0d0d0d;
    --ink: #5b5148;
    --ink-soft: #6c635a;
    --frost-top: #f4f3f2;
    --frost-mid: #dfe6ee;
    --frost-low: #e9dcdc;
  }
  * { margin: 0; padding: 0; box-sizing: border-box; }
  html, body {
    width: 1200px; height: 970px; overflow: hidden;
    background: var(--page-bg);
  }
  .card {
    position: absolute; left: 100px; top: 200px;
    width: 1000px; height: 567px;
    box-shadow: 0 18px 40px rgba(0,0,0,0.25);
  }
  .card-bg { position: absolute; inset: 0; width: 100%; height: 100%; }
  .holder {
    position: absolute; left: 55px; top: 232px;
    font-family: "Cinzel", serif; color: var(--ink);
  }
  .holder-name { font-size: 36px; font-weight: 400; letter-spacing: 1px; line-height: 1; }
  .holder-title {
    font-family: "Questrial", sans-serif; font-size: 24px;
    color: var(--ink-soft); margin-top: 6px;
  }
  .contacts {
    position: absolute; left: 53px; top: 393px; list-style: none;
    font-family: "Questrial", sans-serif; font-size: 23px; color: var(--ink-soft);
  }
  .contacts li { display: flex; align-items: center; height: 35px; }
  .contacts svg { width: 22px; height: 22px; margin-right: 12px; fill: none; stroke: var(--ink); stroke-width: 1.8; }
  .brand {
    position: absolute; left: 565px; top: 230px; width: 340px; text-align: center;
    font-family: "Cinzel", serif; font-weight: 400; color: var(--ink);
  }
  .brand-name { font-size: 32px; line-height: 1; white-space: nowrap; }
  .brand-sub { font-size: 15px; letter-spacing: 7px; margin-top: 6px; }
</style>
</head>
<body>
  <div class="card">
    <svg class="card-bg" viewBox="0 0 1000 567" preserveAspectRatio="none" aria-hidden="true">
      <defs>
        <linearGradient id="frost" x1="0" y1="0" x2="0.6" y2="1">
          <stop offset="0" stop-color="var(--frost-top)"/>
          <stop offset="0.5" stop-color="var(--frost-mid)"/>
          <stop offset="1" stop-color="var(--frost-low)"/>
        </linearGradient>
      </defs>
      <rect class="card-black" width="1000" height="567" fill="var(--card-black)"/>
      <path class="frost-band" d="M0,212 C190,80 580,12 1000,6 L1000,182 C870,400 580,515 290,526 L0,526 Z" fill="url(#frost)"/>
    </svg>

    <div class="holder">
      <div class="holder-name">ALDEN MARSH</div>
      <div class="holder-title">Chief Executive Officer</div>
    </div>

    <ul class="contacts">
      <li>
        <svg viewBox="0 0 24 24"><path d="M6 3 L9 3 L10 8 L8 9.5 C9 12.5 11.5 15 14.5 16 L16 14 L21 15 L21 18 C21 20 19.5 21 17.5 20.5 C10.5 19 5 13.5 3.5 6.5 C3 4.5 4 3 6 3 Z"/></svg>
        <span>44 7700 900482</span>
      </li>
      <li>
        <svg viewBox="0 0 24 24"><rect x="2.5" y="5" width="19" height="14"/><path d="M2.5 5 L12 13 L21.5 5"/></svg>
        <span>td.photography@mailbox.com</span>
      </li>
      <li>
        <svg viewBox="0 0 24 24"><circle cx="12" cy="12" r="9.5"/><path d="M2.5 12 H21.5 M12 2.5 C8 7 8 17 12 21.5 M12 2.5 C16 7 16 17 12 21.5"/></svg>
        <span>www.talvendoraphoto.com</span>
      </li>
    </ul>

    <div class="brand">
      <div class="brand-name">Talven Doroshko</div>
      <div class="brand-sub">PHOTOGRAPHY</div>
    </div>
  </div>
</body>
</html>
```